RW Holloway LLC Business Card - Civil Engineering & Consulting Firm

We need a Business Card that is elegant, and masculine.  It is our Professional Civil Engineering & Consulting Company located in San Antonio TX (Not s construction or builder firm- no gears & no tool images please). We provide civil engineering services including  commercial site plans, grading and drainage plans, utility plans, hydraulics and hydrology, land planning, utility coordination, and other general civil engineering services related to commercial and residential development.
We have 2 existing Logos. We would like to convey reliability, strength, trustworthiness and attention to detail.  Blues and orange tones as per logo We are OK with the use of a darker blue in the mix.  We have 2 logo versions - Full Company Name Logo to go on the back of card, & Small Icon Logo for the front w/ personal Info.

Target Market(s)
Architects, Real Estate Developers, Other Strctural Engineers, Surveyers, General Contractors
Industry/Entity Type
Professional Civil Engineering
Contact Information for Business Card
Name, Position, Address, Cell & Office #, email, and company website
Font styles to use
Other font styles liked:
- Avian
Requirements
Should not have
- No Tools, No Gears, no Cranes, or Construction Equipment.

```html
<!DOCTYPE html>
<html lang="en">
<head>
<meta charset="utf-8">
<title>RW Holloway LLC – Business Card</title>
<link rel="stylesheet" href="https://fonts.googleapis.com/css2?family=Josefin+Sans:wght@300;400&family=Arimo:wght@400&display=swap">
<style>
  :root {
    --bg: #c9c9c9;
    --orange: #f0922b;
    --blue: #7aaedb;
    --blue-text: #6b9fd3;
    --ink: #151515;
    --paper: #ffffff;
  }
  * { margin: 0; padding: 0; box-sizing: border-box; }
  html, body { width: 1200px; height: 900px; overflow: hidden; }
  body {
    background: var(--bg);
    position: relative;
    font-family: "Arimo", Arial, sans-serif;
  }
  .card {
    position: absolute;
    width: 620px;
    height: 354px;
    border-radius: 34px;
    overflow: hidden;
    box-shadow: 0 6px 14px rgba(0,0,0,0.35);
  }
  .card--front {
    left: 90px; top: 80px;
    background: linear-gradient(180deg, var(--orange) 0%, #d79a5a 35%, #a0a8ad 62%, var(--blue) 88%);
    display: flex; align-items: center; justify-content: center;
  }
  .wordmark {
    font-family: "Josefin Sans", sans-serif;
    font-weight: 300;
    letter-spacing: 0.04em;
    text-transform: uppercase;
    white-space: nowrap;
  }
  .card--front .wordmark { color: var(--paper); font-size: 50px; }

  .card--back { left: 490px; top: 466px; background: var(--paper); }
  .card--back .wordmark {
    position: absolute; left: 46px; top: 64px;
    color: var(--blue-text); font-size: 38px;
  }
  .person { position: absolute; left: 56px; top: 170px; }
  .person__name {
    font-family: "Josefin Sans", sans-serif;
    font-weight: 400; font-size: 27px; text-transform: uppercase;
    color: var(--blue-text); letter-spacing: 0.02em;
  }
  .person__name .surname { color: var(--orange); }
  .person__role { font-size: 17px; color: var(--ink); margin-top: 2px; }
  .contacts { position: absolute; left: 56px; top: 248px; list-style: none; }
  .contacts li {
    display: flex; align-items: center; gap: 10px;
    font-size: 18px; color: var(--ink); line-height: 28px;
  }
  .contacts svg { width: 18px; height: 18px; flex: none; }
  .contacts .accent { color: var(--orange); }
  .address {
    position: absolute; right: 40px; top: 150px;
    text-align: right; font-size: 16px; line-height: 22px; color: var(--ink);
  }
</style>
</head>
<body>
  <section class="card card--front" aria-label="Card front">
    <p class="wordmark">RW Holloway LLC</p>
  </section>

  <section class="card card--back" aria-label="Card back">
    <p class="wordmark">RW Holloway LLC</p>

    <div class="person">
      <p class="person__name">Marcus <span class="surname">Reed</span></p>
      <p class="person__role">Managing Director</p>
    </div>

    <ul class="contacts">
      <li>
        <svg viewBox="0 0 20 20" aria-hidden="true"><path d="M5 2 L8 6 L6 8 C7 11 9 13 12 14 L14 12 L18 15 L16 18 C9 18 2 11 2 4 Z" fill="none" stroke="#6b9fd3" stroke-width="2"/></svg>
        210-555 014 732
      </li>
      <li>
        <svg viewBox="0 0 20 20" aria-hidden="true"><rect x="2" y="4" width="16" height="12" fill="#6b9fd3"/><path d="M2 4 L10 11 L18 4" fill="none" stroke="#fff" stroke-width="1.5"/></svg>
        info@hollowayeng.com
      </li>
      <li>
        <svg viewBox="0 0 20 20" aria-hidden="true"><g fill="none" stroke="#6b9fd3" stroke-width="1.5"><circle cx="10" cy="10" r="8"/><ellipse cx="10" cy="10" rx="3.5" ry="8"/><path d="M2 10 H18 M4 6 H16 M4 14 H16"/></g></svg>
        <span>www.<span class="accent">hollowayeng</span>.com</span>
      </li>
    </ul>

    <p class="address">318 Alamo Ridge Drive<br>San Antonio, TX 78205</p>
  </section>
</body>
</html>
```